Logo and Card design for KRV Home Solutions LLC

I need an edgier logo and business card designs. Current logo attached. I like the colors below. I would like the logo to incorporate a home in the design.
Title = Principal-Acquisitions
Email:KRVHOMESOLUTIONS@fernmail.example
555-214-0937
facebook
IG
2 sided business card with the front being contact info a slogan about selling a home fast. The back incorporating What we do. Buy houses, land, or commercial property as is. We find solutions to make the process of selling simple and fair.

Target Market(s)

Motivated house sellers.

Industry/Entity Type

Business

Contact Information for Business Card

Who we are: We are a Faith based Real Estate Investment Company. We pay cash for homes in any condition and can close quick. Whatever the reason you need to sell fast, we can help. We believe in creating win-win solutions to help you in your time of need. We care! We can help!

Logo Text

KRV Home Solutions LLC

Font styles to use
Sans Serif

Colors
33a6d7
0355a3
85abd2
cee9f5
9d9d9d
b2b2b2
ffffff

Requirements
Must have
• Old logo attached. I want something edgier.
• Company name, phone number, description on the back of what we can do. Pay all cash. Buy in as is condition. No fees,Commisions or closing costs.Close quick. No hassles with solutions to meet your unique situation.
• Call today for an offer within 24 hours.

```html
<!DOCTYPE html>
<html lang="en">
<head>
<meta charset="utf-8">
<title>KRV Home Solutions – Business Card</title>
<link rel="stylesheet" href="https://fonts.googleapis.com/css2?family=Roboto:wght@400;500;700&family=Roboto+Condensed:wght@400;700&display=swap">
<style>
  :root {
    --navy: #1e3568;
    --band: #1f3a78;
    --ink: #333a44;
    --white: #ffffff;
    --stage: #2e2e2e;
    --sky: #e9eef0;
    --lawn: #cfd9b0;
  }
  html, body {
    margin: 0;
    width: 1200px;
    height: 960px;
    overflow: hidden;
    background: var(--stage);
    font-family: "Roboto", sans-serif;
  }
  .card {
    position: absolute;
    width: 600px;
    height: 343px;
    overflow: hidden;
  }
  .card-front { left: 314px; top: 113px; }
  .card-back { left: 311px; top: 472px; background: var(--navy); color: var(--white); }

  .front-photo {
    position: absolute; inset: 0;
    background: linear-gradient(180deg, var(--sky) 0%, #e2e7e1 45%, #d8e0c4 75%, var(--lawn) 100%);
  }
  .name-band {
    position: absolute; left: 0; top: 105px; width: 600px; height: 57px;
    background: var(--band);
  }
  .person { position: absolute; left: 33px; top: 112px; color: var(--white); }
  .person-name {
    font-family: "Roboto Condensed", sans-serif; font-weight: 700;
    font-size: 23px; line-height: 26px; margin: 0; letter-spacing: 0.3px;
  }
  .person-title { font-weight: 500; font-size: 15px; line-height: 18px; margin: 0; }

  .brand-front {
    position: absolute; right: 40px; top: 105px; height: 57px;
    display: flex; align-items: center; gap: 8px;
    color: var(--white); font-weight: 700; font-size: 22px; letter-spacing: 0.5px;
  }
  .brand-mark { width: 10px; height: 10px; background: var(--white); }

  .contact-list {
    position: absolute; left: 33px; top: 259px; margin: 0; padding: 0; list-style: none;
    font-size: 14px; color: var(--ink); white-space: nowrap;
  }
  .contact-list li { display: flex; align-items: center; gap: 8px; height: 19.5px; }
  .contact-list svg { width: 13px; height: 13px; fill: var(--band); flex: none; }

  .offer-list {
    position: absolute; right: 30px; top: 227px; margin: 0; padding: 0; list-style: none;
    font-family: "Roboto Condensed", sans-serif; font-size: 14px; color: var(--ink);
    text-align: right; line-height: 18px; white-space: nowrap;
  }
  .offer-list li { position: relative; padding-right: 14px; }
  .offer-list li.bullet::after {
    content: ""; position: absolute; right: 0; top: 8px;
    width: 4px; height: 4px; border-radius: 50%; background: var(--band);
  }

  .brand-back {
    position: absolute; left: 0; right: 0; top: 85px;
    display: flex; justify-content: center; align-items: center; gap: 10px;
    font-weight: 700; font-size: 28px; letter-spacing: 0.6px;
  }
  .brand-back .brand-mark { width: 12px; height: 12px; }
  .back-section { position: absolute; left: 20px; right: 20px; text-align: center; }
  .who { top: 168px; }
  .what { top: 254px; }
  .section-heading { margin: 0 0 3px; font-size: 15.5px; font-weight: 500; line-height: 20px; }
  .section-text { margin: 0; font-size: 15px; line-height: 18px; }
</style>
</head>
<body>
  <section class="card card-front">
    <div class="front-photo" role="img" aria-label="Soft faded photo of a suburban two-storey house with a green lawn and garden path"></div>
    <div class="name-band"></div>
    <div class="person">
      <p class="person-name">MARCUS HALE</p>
      <p class="person-title">Principal-Acquisitions</p>
    </div>
    <div class="brand-front"><span class="brand-mark"></span>KRV HOME SOLUTIONS</div>
    <ul class="contact-list">
      <li><svg viewBox="0 0 24 24"><path d="M6.6 10.8a15.1 15.1 0 0 0 6.6 6.6l2.2-2.2a1 1 0 0 1 1-.25 11.4 11.4 0 0 0 3.6.57 1 1 0 0 1 1 1V20a1 1 0 0 1-1 1A17 17 0 0 1 3 4a1 1 0 0 1 1-1h3.5a1 1 0 0 1 1 1c0 1.25.2 2.45.57 3.57a1 1 0 0 1-.25 1z"/></svg>555-214-0937</li>
      <li><svg viewBox="0 0 24 24"><path d="M2 5h20v14H2z"/><path d="M3 6l9 6.3L21 6v1.5l-9 6.3-9-6.3z" fill="#fff"/></svg>KRVHOMESOLUTIONS@fernmail.example</li>
      <li><svg viewBox="0 0 24 24"><circle cx="12" cy="12" r="10"/><path d="M2 12h20M12 2c3 3 3 17 0 20M12 2c-3 3-3 17 0 20" stroke="#fff" stroke-width="1.5" fill="none"/></svg>KRVHOMESOLUTIONS.example</li>
    </ul>
    <ul class="offer-list">
      <li class="bullet">Pay all cash. Buy in as is condition</li>
      <li class="bullet">No fees,Commisions or closing costs</li>
      <li class="bullet">Close quick. No hassles with</li>
      <li>solutions to meet your unique situation</li>
      <li class="bullet">Call today for an offer within 24 hours</li>
    </ul>
  </section>

  <section class="card card-back">
    <div class="brand-back"><span class="brand-mark"></span>KRV HOME SOLUTIONS</div>
    <div class="back-section who">
      <h2 class="section-heading">WHO WE ARE</h2>
      <p class="section-text">We are a Faith based Real Estate Investment Company. We pay cash for<br>homes in any condition and can close quick. Whatever the reason you need<br>to sell fast, we can help. We believe in creating win-win solutions to help</p>
    </div>
    <div class="back-section what">
      <h2 class="section-heading">WHAT WE DO</h2>
      <p class="section-text">Buy houses, land, or commercial property as is.<br>We find solutions to make the process of selling simple and fair.</p>
    </div>
  </section>
</body>
</html>
```